Business card for law firm

Need business card for new law firm. Think confident, authoritative, conservative, but not stuffy or old-fashioned.

Contact Information for Business Card

Content for card - logo (uploaded), plus the following:

Paul Whitcombe (larger font)
Managing Partner (larger font, but not as large as name)
Level 9, 7 Ferris Lane
Sydney NSW 2000
Main Tel 02 9364 2710
Direct Tel 02 8472 3159
Email paul@qvlegal.com.au
www.qvlegal.com.au

Letterhead design should include logo plus:
Level 9, 7 Ferris Lane
Sydney NSW 2000
Tel 02 8472 3159
www.qvlegal.com.au

```html
<!DOCTYPE html>
<html lang="en">
<head>
<meta charset="utf-8">
<title>Quayvale Legal – Business Card</title>
<link rel="stylesheet" href="https://fonts.googleapis.com/css2?family=Open+Sans:wght@400;600&family=Roboto:wght@500;700&display=swap">
<style>
  :root {
    --navy: #0b1d57;
    --paper: #ffffff;
    --ink: #1a1a1a;
    --muted: #4a4a4a;
    --rule: #6b6b6b;
    --backdrop: #e4e4e4;
  }
  * { margin: 0; padding: 0; box-sizing: border-box; }
  html, body { width: 1146px; height: 1200px; overflow: hidden; }
  body {
    background: var(--backdrop);
    position: relative;
    font-family: "Open Sans", sans-serif;
  }
  .card {
    position: absolute;
    left: 206px;
    width: 731px;
    height: 420px;
  }
  .card-front { top: 124px; background: var(--paper); }
  .card-back { top: 654px; background: var(--navy); }

  .brand {
    display: flex;
    flex-direction: column;
    align-items: center;
    gap: 18px;
    font-family: "Open Sans", sans-serif;
    font-weight: 400;
    letter-spacing: 3px;
    text-transform: uppercase;
  }
  .brand-mark { width: 42px; height: 42px; }
  .brand-name { font-size: 30px; line-height: 1; }

  .card-front .brand {
    position: absolute;
    right: 42px;
    top: 46px;
    color: var(--navy);
  }
  .card-front .brand-mark { background: var(--navy); }

  .card-back .brand {
    position: absolute;
    left: 0; right: 0;
    top: 150px;
    color: var(--paper);
  }
  .card-back .brand-mark { background: var(--paper); }

  .holder {
    position: absolute;
    left: 36px;
    top: 238px;
  }
  .holder-name {
    font-family: "Roboto", sans-serif;
    font-weight: 700;
    font-size: 34px;
    line-height: 1;
    color: var(--navy);
  }
  .holder-role {
    font-family: "Roboto", sans-serif;
    font-weight: 500;
    font-size: 20px;
    line-height: 1;
    margin-top: 6px;
    color: var(--ink);
  }

  .divider {
    position: absolute;
    left: 36px;
    top: 313px;
    width: 653px;
    height: 1px;
    background: var(--rule);
  }
  .divider-accent {
    position: absolute;
    left: 0;
    top: -3px;
    width: 166px;
    height: 5px;
    background: var(--navy);
  }

  .contact {
    position: absolute;
    top: 330px;
    font-size: 16px;
    line-height: 21.5px;
    color: var(--muted);
  }
  .contact-personal { left: 36px; }
  .contact-office { right: 42px; text-align: right; }
  .contact-web { font-weight: 600; color: var(--ink); }
</style>
</head>
<body>

  <section class="card card-front">
    <div class="brand">
      <span class="brand-mark"></span>
      <span class="brand-name">Quayvale Legal</span>
    </div>

    <div class="holder">
      <p class="holder-name">Paul Whitcombe</p>
      <p class="holder-role">Managing Partner</p>
    </div>

    <div class="divider"><span class="divider-accent"></span></div>

    <div class="contact contact-personal">
      <p>02 9364 2710 (Main)</p>
      <p>02 8472 3159 (Direct)</p>
      <p>paul@qvlegal.com.au</p>
    </div>

    <div class="contact contact-office">
      <p>Level 9, 7 Ferris Lane</p>
      <p>Sydney NSW 2000</p>
      <p class="contact-web">www.qvlegal.com.au</p>
    </div>
  </section>

  <section class="card card-back">
    <div class="brand">
      <span class="brand-mark"></span>
      <span class="brand-name">Quayvale Legal</span>
    </div>
  </section>

</body>
</html>
```